Birchline Septic Solutions

Would like to see some single sided ones but would also like to see some double sided with one sided only being the logo. Owners name is Colin Vandro. Phone number is 555-214-0387
Services are pumping, inspections, installs, and repairs

Contact Information for Business Card

555-241-0387 Colin Vandro Greenfield, OH

```html
<!DOCTYPE html>
<html lang="en">
<head>
<meta charset="utf-8">
<title>Birchline Septic Solutions – Business Card</title>
<link rel="stylesheet" href="https://fonts.googleapis.com/css2?family=Montserrat:wght@500;700;800&display=swap">
<style>
  :root {
    --bg: #3b3b3d;
    --card-white: #ffffff;
    --card-black: #0d0d0d;
    --teal: #1fbfb8;
    --ink: #1a1a1a;
    --white: #ffffff;
  }
  * { box-sizing: border-box; margin: 0; padding: 0; }
  html, body {
    width: 1200px; height: 1200px; overflow: hidden;
    background: var(--bg);
    font-family: "Montserrat", sans-serif;
  }
  .stage {
    position: relative; width: 1200px; height: 1200px;
  }
  .card {
    position: absolute; left: 220px;
    width: 760px; height: 434px;
    border-radius: 30px; overflow: hidden;
    box-shadow: 0 14px 30px rgba(0,0,0,0.35);
  }
  .card--front { top: 130px; background: var(--card-white); }
  .card--back { top: 636px; background: var(--card-black); }

  .wave { position: absolute; inset: 0; width: 100%; height: 100%; }

  .brand {
    position: absolute; font-weight: 800; text-transform: uppercase;
    line-height: 1;
  }
  .card--front .brand { top: 78px; right: 60px; color: var(--ink); text-align: center; }
  .brand__name { display: block; font-size: 56px; letter-spacing: 1px; }
  .brand__tag { display: block; font-size: 19px; letter-spacing: 6px; margin-top: 10px; }

  .card--back .brand {
    left: 0; right: 0; top: 150px; text-align: center; color: var(--white);
  }
  .card--back .brand__name { font-size: 86px; }
  .card--back .brand__tag { font-size: 26px; letter-spacing: 9px; margin-top: 16px; }

  .person { position: absolute; left: 56px; top: 176px; }
  .person__name {
    color: var(--teal); font-weight: 700; font-size: 38px;
    text-transform: uppercase; letter-spacing: -0.5px; line-height: 1;
  }
  .person__role {
    color: var(--ink); font-weight: 500; font-size: 22px;
    text-transform: uppercase; margin-top: 2px;
  }
  .contact { list-style: none; margin-top: 16px; }
  .contact__item {
    display: flex; align-items: center; gap: 12px;
    font-size: 20px; color: var(--ink); font-weight: 500; height: 30px;
  }
  .contact__icon { width: 22px; height: 22px; flex: none; }
</style>
</head>
<body>
<main class="stage">

  <section class="card card--front" aria-label="Business card front">
    <svg class="wave" viewBox="0 0 760 434" preserveAspectRatio="none" aria-hidden="true">
      <path fill="var(--teal)" transform="translate(-22,-24)"
            d="M170 458 C260 350 420 380 560 320 S730 160 790 130 L790 458 Z"/>
      <path fill="var(--card-white)" transform="translate(-9,-10)"
            d="M170 444 C260 340 420 370 560 310 S730 150 780 122 L780 444 Z"/>
      <path fill="var(--card-black)"
            d="M170 434 C260 330 420 360 560 300 S730 140 760 112 L760 434 Z"/>
    </svg>

    <div class="brand">
      <span class="brand__name">Birchline</span>
      <span class="brand__tag">Septic Solutions</span>
    </div>

    <div class="person">
      <p class="person__name">Colin Vandro</p>
      <p class="person__role">Owner</p>
      <ul class="contact">
        <li class="contact__item">
          <svg class="contact__icon" viewBox="0 0 24 24" aria-hidden="true"><path fill="var(--teal)" d="M6.6 10.8a15.1 15.1 0 0 0 6.6 6.6l2.2-2.2a1 1 0 0 1 1-.25 11.4 11.4 0 0 0 3.6.57 1 1 0 0 1 1 1V20a1 1 0 0 1-1 1A17 17 0 0 1 3 4a1 1 0 0 1 1-1h3.5a1 1 0 0 1 1 1c0 1.25.2 2.45.57 3.57a1 1 0 0 1-.25 1z"/></svg>
          555-214-0387
        </li>
        <li class="contact__item">
          <svg class="contact__icon" viewBox="0 0 24 24" aria-hidden="true"><rect x="2" y="5" width="20" height="14" rx="1" fill="var(--teal)"/><path d="M2.5 5.5 12 13l9.5-7.5" fill="none" stroke="#fff" stroke-width="1.6"/></svg>
          info@birchlineseptic.com
        </li>
        <li class="contact__item">
          <svg class="contact__icon" viewBox="0 0 24 24" aria-hidden="true"><g fill="none" stroke="var(--teal)" stroke-width="1.8"><circle cx="12" cy="12" r="9.5"/><ellipse cx="12" cy="12" rx="4" ry="9.5"/><path d="M2.5 12h19M4 7h16M4 17h16"/></g></svg>
          www.birchlineseptic.com
        </li>
      </ul>
    </div>
  </section>

  <section class="card card--back" aria-label="Business card back">
    <div class="brand">
      <span class="brand__name">Birchline</span>
      <span class="brand__tag">Septic Solutions</span>
    </div>
  </section>

</main>
</body>
</html>
```